Car rental website design for a UAE car rental company

This project is about creating a new website design for a car rental company located in Dubai (United Arab Emirates), I opened the same project a few months ago but I didn't receive a lot of appealing entries so I closed it but this time I am marking the project as guaranteed to avoid such situation again, if you have already provided a design before then please re-submit again on this project so that it is considered while reviewing all the designs

A few important things:

1- We need a simple non-complex design
2- The final deliverable would be 2 screens (PSD, JPEG ... etc), the first screen is for the home page and the second screen is for an internal page
3- The home page must have a section that end users can use to rent a car online directly from the home page instead of going into some inner pages
4- The current website is very old and not very appealing so avoid creating a similar design (www.crestvane-autos.example)
5- The name is Crestvane but the company rents normal cars (no Limousin cars will be rented) so avoid adding any fancy cars in the images/graphics used in the design, just normal end users cars
6- The expected pages would be: home, About us, Our team, Strategy, Contact us and links to social media pages
7- The attachments include the company's logo and some screens from other car rental companies that provide online rentals/payments

If you have any questions please feel free to ask and please note that we will need the designs urgently

Thanks

Target Market(s)

Dubai - United Arab Emirates

Industry/Entity Type

It Company

Number of Pages Required

2 page

Font styles to use
Sans Serif

Requirements
Must have
• Check the project details
Nice to have
Should not have

```html
<!DOCTYPE html>
<html lang="en">
<head>
<meta charset="utf-8">
<title>Crestvane Rent A Car</title>
<link href="https://fonts.googleapis.com/css2?family=Roboto:wght@400;500;700&family=Roboto+Condensed:wght@400;500;700&display=swap" rel="stylesheet">
<style>
:root{
  --crimson:#a5093a;
  --ink:#111;
  --text:#333;
  --grey-tab:#a9b5ad;
  --bg-bottom:#8e9c95;
  --field-line:#c9c9c9;
  --white:#fff;
}
*{box-sizing:border-box;margin:0;padding:0}
html,body{width:1200px;height:798px;overflow:hidden}
body{font-family:"Roboto",Arial,sans-serif;color:var(--text);position:relative;
  background:linear-gradient(180deg,#e9ecea 105px,#dfe4e1 300px,#b9c3be 600px,var(--bg-bottom) 798px)}
.abs{position:absolute}
.site-header{left:0;top:0;width:1200px;height:106px;background:var(--white);border-bottom:3px solid var(--crimson);z-index:3}
.brand{left:128px;top:12px;width:120px;text-align:center}
.brand-mark{width:40px;height:40px;border:2px solid var(--crimson);margin:0 auto 6px}
.brand-name{font-size:22px;color:#7d7f7e;line-height:1}
.contact{top:22px;font-family:"Roboto Condensed",sans-serif;font-size:15.5px;color:#555;display:flex;align-items:center;gap:7px}
.contact svg{width:16px;height:16px}
.main-nav{left:350px;top:62px;width:612px;height:46px;background:var(--crimson);
  clip-path:polygon(8px 0,100% 0,100% 100%,0 100%,0 8px);display:flex;align-items:center;padding-left:36px;gap:26px}
.main-nav a{color:var(--white);text-decoration:none;font-family:"Roboto Condensed",sans-serif;font-weight:500;font-size:16px;display:flex;align-items:center;gap:6px}
.main-nav svg{width:15px;height:15px;fill:var(--white)}
.account{left:960px;top:62px;width:166px;height:46px;background:#0d0d0d;color:var(--white);
  font-family:"Roboto Condensed",sans-serif;font-weight:500;font-size:16px;display:flex;align-items:center;justify-content:center}
.hero-disc{left:524px;top:130px;width:620px;height:620px;border-radius:50%;
  background:radial-gradient(circle at 48% 50%,#fff 0,#f7f7f7 55%,#ededed 100%)}
.hero-title{right:197px;top:192px;text-align:right}
.hero-title h1{font-weight:700;font-size:58px;color:var(--ink);line-height:1;letter-spacing:-1px}
.hero-title h1 span{color:var(--crimson)}
.hero-title p{font-family:"Roboto Condensed",sans-serif;font-size:19px;color:#444;margin-top:2px}
.hero-copy{right:197px;top:294px;width:400px;text-align:right;font-family:"Roboto Condensed",sans-serif;font-size:14.8px;line-height:22px;color:#555;z-index:2}
.hero-car{left:604px;top:408px;width:518px;height:298px;border-radius:140px 150px 60px 60px/120px 130px 40px 40px;
  background:linear-gradient(180deg,#f58a3a 0%,#e4651b 60%,#b94c12 100%)}
.booking{left:74px;top:151px;width:524px;height:545px;background:var(--white);box-shadow:0 2px 6px rgba(0,0,0,.15);z-index:1}
.tab{top:0;height:53px;display:flex;align-items:center;justify-content:center;font-family:"Roboto Condensed",sans-serif;font-size:16px;color:var(--white)}
.tab-active{left:2px;width:167px;background:var(--crimson);top:-2px;height:55px}
.tab-active::after{content:"";position:absolute;left:76px;bottom:-9px;border:9px solid transparent;border-bottom:0;border-top-color:var(--crimson)}
.tab-idle{left:172px;width:350px;background:var(--grey-tab)}
.step{left:28px;width:34px;height:40px;border:2px solid var(--crimson);font-family:"Roboto Condensed",sans-serif;font-size:19px;color:var(--crimson);display:flex;align-items:center;justify-content:center;outline:1px solid #ddd;outline-offset:2px}
.label{left:76px;font-family:"Roboto Condensed",sans-serif;font-size:15.5px;color:var(--ink);font-weight:500;display:flex;align-items:center;gap:5px}
.label small{font-size:12px;color:#555;font-weight:400}
.link{left:76px;font-size:12px;color:var(--crimson)}
.field{left:76px;height:31px;border:1px solid var(--field-line);background:var(--white);border-radius:2px;font-size:12px;color:#777;display:flex;align-items:center;justify-content:space-between;padding:0 10px}
.field svg{width:14px;height:14px}
.check{left:76px;font-size:12px;color:#555;display:flex;align-items:center;gap:8px}
.check .box{width:12px;height:12px;border:1px solid #aaa;background:#eee}
.help{width:17px;height:17px;border-radius:50%;background:#b4b4b4;color:#fff;font-size:11px;font-weight:700;display:inline-flex;align-items:center;justify-content:center}
.quote-btn{left:76px;top:477px;width:305px;height:39px;background:var(--crimson);color:var(--white);font-family:"Roboto Condensed",sans-serif;font-weight:500;font-size:16px;display:flex;align-items:center;justify-content:center}
.newsletter{left:75px;top:735px;display:flex;gap:14px;align-items:center;color:var(--white);z-index:2}
.newsletter svg{width:58px;height:32px}
.newsletter h3{font-family:"Roboto Condensed",sans-serif;font-weight:500;font-size:15.5px}
.newsletter p{font-size:12px}
.signup{left:455px;top:738px;display:flex;z-index:2}
.signup .input{width:238px;height:31px;background:var(--white);font-size:12px;color:#666;display:flex;align-items:center;padding-left:11px}
.signup .btn{width:73px;height:31px;background:#0d0d0d;color:#fff;font-family:"Roboto Condensed",sans-serif;font-size:13.5px;display:flex;align-items:center;justify-content:center}
.social{left:989px;top:731px;display:flex;gap:5px;z-index:2}
.social span{width:24px;height:24px;border-radius:50%;background:#d3d9d5}
.copyright{left:913px;top:762px;font-size:12px;color:var(--white);z-index:2}
</style>
</head>
<body>
<header class="site-header abs">
  <div class="brand abs">
    <div class="brand-mark"></div>
    <div class="brand-name">Crestvane</div>
  </div>
  <div class="contact abs" style="left:811px">
    <svg viewBox="0 0 24 24"><path d="M6.6 10.8a15 15 0 006.6 6.6l2.2-2.2c.3-.3.7-.4 1-.2 1.1.4 2.3.6 3.6.6.6 0 1 .4 1 1V20c0 .6-.4 1-1 1A17 17 0 013 4c0-.6.4-1 1-1h3.5c.6 0 1 .4 1 1 0 1.3.2 2.5.6 3.6.1.3 0 .7-.2 1z" fill="#888"/></svg>
    971 4 555 0182
  </div>
  <div class="contact abs" style="left:956px">
    <svg viewBox="0 0 24 24"><path d="M3 6h18v12H3z M3 6l9 7 9-7" fill="none" stroke="#888" stroke-width="1.6"/></svg>
    INFO@CRESTVANE.EXAMPLE
  </div>
  <nav class="main-nav abs">
    <a href="#"><svg viewBox="0 0 16 16"><path d="M8 1l7 6h-2v7H9V10H7v4H3V7H1z"/></svg>HOME</a>
    <a href="#"><svg viewBox="0 0 16 16"><circle cx="8" cy="5" r="3.5"/><path d="M2 15c0-4 3-6 6-6s6 2 6 6z"/></svg>ABOUT</a>
    <a href="#"><svg viewBox="0 0 20 16"><circle cx="5" cy="6" r="2.5"/><circle cx="10" cy="5" r="3"/><circle cx="15" cy="6" r="2.5"/><path d="M0 14c0-3 2-5 5-5s5 2 5 5zM10 14c0-3 2-5 5-5s5 2 5 5z"/></svg>OUR TEAM</a>
    <a href="#"><svg viewBox="0 0 16 16"><path d="M8 1a6 6 0 00-3 11v3h6v-3A6 6 0 008 1z"/></svg>STRATEGY</a>
    <a href="#"><svg viewBox="0 0 24 16"><path d="M6 2h18v12H6zM0 5h5v1H0zM1 8h4v1H1zM2 11h3v1H2z"/></svg>CONTACT</a>
  </nav>
  <div class="account abs">LOGIN&nbsp;|&nbsp;REGISTER</div>
</header>

<div class="hero-disc abs"></div>
<div class="hero-title abs">
  <h1>Crest<span>vane</span></h1>
  <p>RENT A CAR</p>
</div>
<p class="hero-copy abs">AS DUBAI IS EXPECTED TO WELCOME MILLIONS OF TOURISTS AND VISITORS, CAR RENTAL INDUSTRY IS BELIEVED TO ESCALATE MORE RAPIDLY IN THE REGION.</p>
<div class="hero-car abs" role="img" aria-label="Orange family sedan photographed in three-quarter front view"></div>

<section class="booking abs">
  <div class="tab tab-active abs">BOOK A CAR</div>
  <div class="tab tab-idle abs">VIEW/MODIFY/CANCEL A RESERVATION</div>

  <div class="step abs" style="top:80px">01</div>
  <div class="label abs" style="top:78px">PICK-UP LOCATION <small>(City,State or Airport Code)</small></div>
  <div class="link abs" style="top:99px">Previous Searches</div>
  <div class="field abs" style="top:124px;width:305px"></div>
  <div class="link abs" style="top:160px">Help me find a rental location</div>
  <div class="check abs" style="top:183px"><span class="box"></span>Return car to different Crestvane location <span class="help">?</span></div>

  <div class="step abs" style="top:228px">02</div>
  <div class="label abs" style="top:224px">PICK-UP DATE AND TIME:</div>
  <div class="field abs" style="top:247px;width:148px">DD/MM/YY<svg viewBox="0 0 14 14"><rect x="1" y="2" width="12" height="11" fill="none" stroke="#bbb"/><path d="M1 5h12" stroke="#bbb"/></svg></div>
  <div class="field abs" style="top:247px;left:233px;width:148px">HH:MM<svg viewBox="0 0 14 14"><path d="M4 6l3-3 3 3M4 9l3 3 3-3" fill="none" stroke="#bbb"/></svg></div>
  <div class="label abs" style="top:294px">RETURN DATE AND TIME:</div>
  <div class="field abs" style="top:317px;width:148px">DD/MM/YY<svg viewBox="0 0 14 14"><rect x="1" y="2" width="12" height="11" fill="none" stroke="#bbb"/><path d="M1 5h12" stroke="#bbb"/></svg></div>
  <div class="field abs" style="top:317px;left:233px;width:148px">HH:MM<svg viewBox="0 0 14 14"><path d="M4 6l3-3 3 3M4 9l3 3 3-3" fill="none" stroke="#bbb"/></svg></div>

  <div class="label abs" style="top:370px">HIRE CAR TYPE: <span class="help">?</span></div>
  <div class="field abs" style="top:399px;width:305px">Show Me All<svg viewBox="0 0 14 14"><path d="M2 5l5 5 5-5" fill="none" stroke="#555" stroke-width="1.5"/></svg></div>
  <div class="check abs" style="top:442px"><span class="box"></span>Apply a discount code <span class="help">?</span></div>
  <div class="quote-btn abs">GET A QUOTE</div>
</section>

<footer>
  <div class="newsletter abs">
    <svg viewBox="0 0 58 32"><path d="M22 4h34v24H22zM22 4l17 13 17-13" fill="none" stroke="#fff" stroke-width="1.6"/><path d="M2 10h16M6 16h12M10 22h8" stroke="#fff" stroke-width="1.6"/></svg>
    <div><h3>SIGN UP TO CRESTVANE EMAIL NEWSLETTER</h3><p>Enter your email &amp; give me latest news &amp; updates</p></div>
  </div>
  <div class="signup abs"><div class="input">Enter your email</div><div class="btn">SIGN UP</div></div>
  <div class="social abs"><span></span><span></span><span></span><span></span><span></span></div>
  <div class="copyright abs">©2015 Crestvane. All Rights Reserved.</div>
</footer>
</body>
</html>
```